We (R. T. Galvin & Partners, Inc.) are an executive Search firm based in Los Angeles that is exclusively focused in the Med Tech and Health Tech arenas.   I need a logo to communicate that we are a high end search firm, but also that we are focused in the medicine and science arenas called health tech and med tech.  Many of our clients have robotics and artificial intelligence type products, so it is very technology forward.  I tend to gravitate towards clean, sharp aesthetic as opposed to something that is really over the top.
Attached are files with my logo in two different layouts.  In addition to the letterhead and envelope, I also will need an electronic letterhead in Microsoft Word.  I tend to
I look forward to seeing the designs and just let me know if you have any questions.
Dale

```html
<!DOCTYPE html>
<html lang="en">
<head>
<meta charset="utf-8">
<title>R. T. Galvin &amp; Partners — Stationery</title>
<link rel="stylesheet" href="https://fonts.googleapis.com/css2?family=Montserrat:wght@400;500;600&family=Open+Sans:wght@400;600&display=swap">
<style>
  :root {
    --bg: #d9dadc;
    --paper: #f3f4f6;
    --ink: #2b2d31;
    --ink-soft: #4a4d52;
    --blue: #4a9ad6;
    --dark: #2a2b2d;
    --dark-flap: #232425;
    --light-on-dark: #e6e7ea;
  }
  * { box-sizing: border-box; margin: 0; padding: 0; }
  html, body { width: 1200px; height: 882px; overflow: hidden; }
  body { background: var(--bg); position: relative; font-family: "Open Sans", sans-serif; color: var(--ink); }

  .letterhead {
    position: absolute; left: 93px; top: 80px; width: 499px; height: 704px;
    background: var(--paper);
  }
  .brand { position: absolute; display: flex; align-items: center; gap: 9px; }
  .brand-dot { width: 20px; height: 20px; border-radius: 50%; background: var(--blue); flex: none; }
  .brand-name {
    font-family: "Montserrat", sans-serif; font-weight: 500; font-size: 12.5px;
    letter-spacing: 0.3px; color: var(--ink); white-space: nowrap;
  }
  .letterhead .brand { left: 47px; top: 62px; }

  .letter-date { position: absolute; left: 48px; top: 176px; font-size: 8.6px; color: var(--ink-soft); font-weight: 600; }
  .recipient { position: absolute; left: 48px; top: 213px; font-size: 8.6px; line-height: 12px; color: var(--ink-soft); font-weight: 600; }
  .letter-body { position: absolute; left: 47px; top: 283px; width: 404px; font-size: 7.1px; line-height: 12px; color: var(--ink-soft); text-align: justify; }
  .letter-body p + p { margin-top: 12px; }

  .signature { position: absolute; left: 358px; top: 528px; width: 82px; height: 30px; background: linear-gradient(90deg, #e6e7ea, #dcdde0); border-radius: 3px; }
  .signer-role { position: absolute; left: 378px; top: 562px; font-size: 7.6px; color: var(--ink-soft); letter-spacing: 0.2px; }

  .contact { position: absolute; font-family: "Montserrat", sans-serif; font-size: 7.6px; line-height: 10px; color: var(--ink); }
  .contact .firm, .contact .web { color: var(--blue); font-weight: 500; }
  .contact .lines { margin-top: 0; }
  .contact .row { display: flex; align-items: center; gap: 3px; }
  .contact .row + .row { margin-top: 0; }
  .contact .phones { margin-top: 5px; }
  .contact .web { margin-top: 4px; }
  .contact svg { width: 6px; height: 6px; fill: var(--blue); flex: none; }
  .letterhead .contact { left: 50px; top: 595px; }

  .envelope { position: absolute; left: 646px; width: 472px; }
  .envelope-flap { position: absolute; left: 0; top: 0; width: 472px; height: 68px; }
  .envelope-face { position: absolute; left: 0; top: 68px; width: 472px; height: 215px; }
  .envelope .brand { left: 31px; top: 30px; }
  .envelope .contact { left: 28px; top: 122px; }

  .envelope--light { top: 160px; height: 283px; }
  .envelope--light .envelope-face { background: var(--paper); }
  .envelope--light .envelope-flap path { fill: var(--blue); }

  .envelope--dark { top: 501px; height: 283px; }
  .envelope--dark .envelope-face { background: var(--dark); }
  .envelope--dark .envelope-flap path { fill: var(--dark-flap); }
  .envelope--dark .brand-name, .envelope--dark .contact { color: var(--light-on-dark); }
  .envelope--dark .contact .firm, .envelope--dark .contact .web { color: var(--blue); }
</style>
</head>
<body>

<section class="letterhead">
  <div class="brand"><span class="brand-dot"></span><span class="brand-name">R. T. GALVIN &amp; PARTNERS, INC.</span></div>

  <p class="letter-date">Los Angeles, October 12, 2015</p>
  <p class="recipient">Sr.<br>ELENA MARSH<br>Web Master<br>City</p>

  <div class="letter-body">
    <p>Contrary to popular belief, Lorem Ipsum is not simply random text. It has roots in a piece of classical Latin literature from 45 BC, making it over 2000 years old. Howard Lintell, a Latin professor at Ashford College in Vermont, looked up one of the more obscure Latin words, consectetur, from a Lorem Ipsum passage, and going through the cites of the word in classical literature,</p>
    <p>discovered the undoubtable source. Lorem Ipsum comes from sections 1.10.32 and 1.10.33 of "de Finibus Bonorum et Malorum" (The Extremes of Good and Evil) by Lucius Fenn, written in 45 BC. This book is a treatise on the theory of ethics, very popular during the Renaissance. The first line of Lorem Ipsum, "Lorem ipsum dolor sit amet..", comes from a line in section 1.10.32.</p>
    <p>The standard chunk of Lorem Ipsum used since the 1500s is reproduced below for those interested. Sections 1.10.32 and 1.10.33 from "de Finibus Bonorum et Malorum" by Lucius Fenn are also reproduced in their exact original form, accompanied by English versions from the 1914 translation by H. Rowley.</p>
    <p>There are many variations of passages of Lorem Ipsum available, but the majority have suffered alteration in some form, by injected humour, or randomised words which don't look even slightly believable. If you are going to use a passage of Lorem Ipsum, you need to be sure there isn't anything embarrassing hidden in the middle of text. All the Lorem Ipsum generators o</p>
  </div>

  <div class="signature" role="img" aria-label="Handwritten signature of the founder"></div>
  <p class="signer-role">CEO/ FOUNDER</p>

  <div class="contact">
    <div class="firm">R. T. Galvin &amp; Partners, Inc.</div>
    <div>2140 Larkfield Avenue</div>
    <div>Los Angeles, California 90071</div>
    <div class="row phones">
      <svg viewBox="0 0 10 10"><path d="M2 0.5l2 2-1 1.2c.6 1.3 1.6 2.3 2.9 2.9L7 5.6l2 2-1.2 1.6C4.2 9 1 5.8.8 2.2z"/></svg>310-555-0148
      <svg viewBox="0 0 10 10"><path d="M2.5 0h5v3h-5zM0 3.5h10v4H8V10H2V7.5H0z"/></svg>310-555-0192
    </div>
    <div class="row"><svg viewBox="0 0 10 10"><path d="M0 1.5h10v7H0zM.8 2.3L5 5.5l4.2-3.2"/></svg>info@rtgalvinpartners.com</div>
    <div class="web">rtgalvinpartners.com</div>
  </div>
</section>

<section class="envelope envelope--light">
  <svg class="envelope-flap" viewBox="0 0 472 68"><path d="M0 68 L10 22 Q16 2 38 2 L434 2 Q456 2 462 22 L472 68 Z"/></svg>
  <div class="envelope-face">
    <div class="brand"><span class="brand-dot"></span><span class="brand-name">R. T. GALVIN &amp; PARTNERS, INC.</span></div>
    <div class="contact">
      <div class="firm">R. T. Galvin &amp; Partners, Inc.</div>
      <div>2140 Larkfield Avenue</div>
      <div>Los Angeles, California 90071</div>
      <div class="row phones">
        <svg viewBox="0 0 10 10"><path d="M2 0.5l2 2-1 1.2c.6 1.3 1.6 2.3 2.9 2.9L7 5.6l2 2-1.2 1.6C4.2 9 1 5.8.8 2.2z"/></svg>310-555-0148
        <svg viewBox="0 0 10 10"><path d="M2.5 0h5v3h-5zM0 3.5h10v4H8V10H2V7.5H0z"/></svg>310-555-0192
      </div>
      <div class="row"><svg viewBox="0 0 10 10"><path d="M0 1.5h10v7H0zM.8 2.3L5 5.5l4.2-3.2"/></svg>info@rtgalvinpartners.com</div>
      <div class="web">rtgalvinpartners.com</div>
    </div>
  </div>
</section>

<section class="envelope envelope--dark">
  <svg class="envelope-flap" viewBox="0 0 472 68"><path d="M0 68 L10 22 Q16 2 38 2 L434 2 Q456 2 462 22 L472 68 Z"/></svg>
  <div class="envelope-face">
    <div class="brand"><span class="brand-dot"></span><span class="brand-name">R. T. GALVIN &amp; PARTNERS, INC.</span></div>
    <div class="contact">
      <div class="firm">R. T. Galvin &amp; Partners, Inc.</div>
      <div>2140 Larkfield Avenue</div>
      <div>Los Angeles, California 90071</div>
      <div class="row phones">
        <svg viewBox="0 0 10 10"><path d="M2 0.5l2 2-1 1.2c.6 1.3 1.6 2.3 2.9 2.9L7 5.6l2 2-1.2 1.6C4.2 9 1 5.8.8 2.2z"/></svg>310-555-0148
        <svg viewBox="0 0 10 10"><path d="M2.5 0h5v3h-5zM0 3.5h10v4H8V10H2V7.5H0z"/></svg>310-555-0192
      </div>
      <div class="row"><svg viewBox="0 0 10 10"><path d="M0 1.5h10v7H0zM.8 2.3L5 5.5l4.2-3.2"/></svg>info@rtgalvinpartners.com</div>
      <div class="web">rtgalvinpartners.com</div>
    </div>
  </div>
</section>

</body>
</html>
```